Glass Fabricator Presentation Folders

We need a folder to hold information about our company. We fabricate, laminate, temper, and digitally print any design on glass. All of this is done under one roof in our 80,000 square foot facility. Our digital printing is done by Vorn Lume technology, and is the first digital printer in the Southeastern United States. Our customers consist of commercial glaziers, architects, and designers. I have attached our existing logo.

Industry/Entity Type

It Company

Contact Information for Business Card

Harlow Pane Works, LLC
2380NW 42nd Avenue
Pompano Beach, Florida 33069
Phone: 954-615-3871
Fax:954-615-3902
www.harlowpane.example

```html
<!DOCTYPE html>
<html lang="en">
<head>
<meta charset="utf-8">
<title>Harlow Pane Works, LLC — Business Card</title>
<link rel="stylesheet" href="https://fonts.googleapis.com/css2?family=Lato:wght@400;700;900&display=swap">
<style>
  :root {
    --backdrop: #ececec;
    --card-light: #fbfbfb;
    --card-dark: #2b2928;
    --ink: #1c1c1c;
    --ink-soft: #555555;
    --ink-light: #f4f4f4;
    --edge-accent: #c8682c;
  }
  * { margin: 0; padding: 0; box-sizing: border-box; }
  html, body {
    width: 1200px;
    height: 900px;
    overflow: hidden;
    background: var(--backdrop);
    font-family: "Lato", Arial, sans-serif;
  }
  .stage {
    position: relative;
    width: 1200px;
    height: 900px;
  }
  .card {
    position: absolute;
    width: 490px;
    height: 280px;
    border-radius: 3px;
    box-shadow: 0 10px 28px rgba(0,0,0,0.14), 0 2px 5px rgba(0,0,0,0.08);
  }
  .card--front {
    left: 90px;
    top: 380px;
    background: var(--card-light);
    color: var(--ink);
  }
  .card--back {
    left: 620px;
    top: 240px;
    background: var(--card-dark);
    color: var(--ink-light);
    border-bottom: 2px solid var(--edge-accent);
  }
  .holder { position: absolute; left: 34px; top: 30px; }
  .holder__name { font-weight: 900; font-size: 19px; letter-spacing: 0.2px; }
  .holder__role { font-size: 11px; color: var(--ink-soft); margin-top: 2px; }
  .contact { position: absolute; left: 34px; top: 118px; font-size: 11.5px; line-height: 1.3; }
  .contact__label { font-weight: 700; }
  .contact__value { color: var(--ink-soft); }
  .brand {
    position: absolute;
    display: flex;
    align-items: center;
    gap: 9px;
    font-weight: 900;
    text-transform: uppercase;
    letter-spacing: 0.5px;
    white-space: nowrap;
  }
  .brand__mark { width: 16px; height: 16px; background: currentColor; flex: none; }
  .card--front .brand { right: 30px; top: 128px; font-size: 15px; }
  .card--back .brand { left: 50%; top: 50%; transform: translate(-50%, -50%); font-size: 22px; }
  .card--back .brand__mark { width: 22px; height: 22px; }
</style>
</head>
<body>
<main class="stage">
  <section class="card card--front" aria-label="Business card front">
    <div class="holder">
      <p class="holder__name">Marcus Delane</p>
      <p class="holder__role">Managing Director</p>
    </div>
    <div class="contact">
      <p class="contact__label">telephone</p>
      <p class="contact__value">044-615 387 100</p>
      <p class="contact__label">email</p>
      <p class="contact__value">info@harlowpane.example</p>
      <p class="contact__label">address</p>
      <p class="contact__value">2345, adress goes here, country</p>
    </div>
    <div class="brand"><span class="brand__mark"></span><span class="brand__name">Harlow Pane Works, LLC</span></div>
  </section>

  <section class="card card--back" aria-label="Business card back">
    <div class="brand"><span class="brand__mark"></span><span class="brand__name">Harlow Pane Works, LLC</span></div>
  </section>
</main>
</body>
</html>
```